Tech business card design

We need an amazing business card design for our new business 'Pexla' a marketing tech startup based in Sydney, Australia. We provide an online marketplace for businesses to search and buy advertising media, connect with service providers and learn more about marketing. We wish to communicate 'cool tech', reliability and professionalism and design based around our logo.

Target Market(s)

Business Owners

Contact Information for Business Card

Name
Position
Email Address
Website
Phone Number

Font styles to use
Other font styles liked:
• Avenir & Avenir Next

Colors

Designer to choose colors to be used in the design.

```html
<!DOCTYPE html>
<html lang="en">
<head>
<meta charset="UTF-8">
<title>Pexla Business Card</title>
<link rel="stylesheet" href="https://fonts.googleapis.com/css2?family=Mulish:wght@400;500;800&display=swap">
<style>
  :root {
    --backdrop: #3b3b3d;
    --card-navy: #11123f;
    --card-deep: #07081c;
    --tech-glow: #2a2a9a;
    --ink-light: #ffffff;
    --accent-lavender: #b9bff5;
    --shadow: rgba(0, 0, 0, 0.45);
  }
  * { margin: 0; padding: 0; box-sizing: border-box; }
  html, body {
    width: 1200px;
    height: 1000px;
    overflow: hidden;
    background: var(--backdrop);
    font-family: "Mulish", sans-serif;
  }
  .card {
    position: absolute;
    width: 720px;
    height: 410px;
    border-radius: 30px;
    overflow: hidden;
    box-shadow: 0 18px 40px var(--shadow);
  }
  .card-front {
    left: 400px;
    top: 60px;
  }
  .tech-backdrop {
    position: absolute;
    inset: 0;
    background:
      radial-gradient(ellipse at 55% 45%, var(--tech-glow) 0%, #15155a 30%, var(--card-deep) 75%);
  }
  .card-back {
    left: 80px;
    top: 520px;
    background: var(--card-navy);
  }
  .wordmark {
    position: absolute;
    color: var(--ink-light);
    font-weight: 800;
    font-size: 118px;
    letter-spacing: -2px;
    line-height: 1;
  }
  .card-front .wordmark { left: 205px; top: 130px; }
  .card-back .wordmark { left: 390px; top: 70px; font-size: 112px; }
  .tm {
    position: absolute;
    color: var(--ink-light);
    font-size: 13px;
    font-weight: 800;
  }
  .card-front .tm { left: 540px; top: 262px; }
  .card-back .tm { left: 688px; top: 196px; }
  .accent-square {
    position: absolute;
    left: 60px;
    top: 152px;
    width: 18px;
    height: 40px;
    background: var(--accent-lavender);
  }
  .contact-block {
    position: absolute;
    left: 92px;
    top: 150px;
    color: var(--ink-light);
  }
  .person-name { font-size: 24px; font-weight: 500; }
  .person-role { font-size: 15px; font-weight: 400; margin-top: 2px; }
  .contact-list {
    position: absolute;
    left: 52px;
    top: 230px;
    list-style: none;
    color: var(--ink-light);
    font-size: 20px;
  }
  .contact-list li {
    display: flex;
    align-items: center;
    gap: 12px;
    height: 28px;
  }
  .contact-list svg { width: 18px; height: 18px; flex: none; }
</style>
</head>
<body>
  <section class="card card-front">
    <div class="tech-backdrop" role="img" aria-label="Dark blue abstract circuitry and light-streak technology texture"></div>
    <div class="wordmark">Pexla</div>
    <span class="tm">TM</span>
  </section>

  <section class="card card-back">
    <div class="wordmark">Pexla</div>
    <span class="tm">TM</span>
    <div class="accent-square"></div>
    <div class="contact-block">
      <p class="person-name">Marcus Lane</p>
      <p class="person-role">Managing Director</p>
    </div>
    <ul class="contact-list">
      <li>
        <svg viewBox="0 0 24 24" fill="none" stroke="#fff" stroke-width="2"><path d="M5 3h4l2 5-3 2a12 12 0 0 0 6 6l2-3 5 2v4a2 2 0 0 1-2 2A18 18 0 0 1 3 5a2 2 0 0 1 2-2z"/></svg>
        <span>800-214-0375</span>
      </li>
      <li>
        <svg viewBox="0 0 24 24" fill="none" stroke="#fff" stroke-width="2"><rect x="2" y="5" width="20" height="14" rx="1"/><path d="M2 6l10 7 10-7"/></svg>
        <span>marcus@pexlamail.com</span>
      </li>
      <li>
        <svg viewBox="0 0 24 24" fill="none" stroke="#fff" stroke-width="2"><circle cx="12" cy="12" r="10"/><path d="M2 12h20M12 2c3 3 3 17 0 20M12 2c-3 3-3 17 0 20"/></svg>
        <span>www.pexla.com</span>
      </li>
    </ul>
  </section>
</body>
</html>
```